Naturopath Practitioner Card Design

I am a naturopath needing a design for a business card mainly to show that I am a naturopath and have some contact details to give to prospective clients. I am open minded about the design and what is on the second side of the card whether it just be some artwork or space for details, appointment times etc. Naturopathy is the practice of natural medicine that uses a holistic approach and incorporates herbal and nutritional medicine.

Industry/Entity Type

Business

Contact Information for Business Card

Tom Rudd NaturopathBHSc (Naturopathy) Member WHPG 0487 925 316 tom.rudd@mailexample.com www.tomruddnaturopathy.example.au

Requirements
Nice to have
• Would prefer some kind of original pattern/art work/logo rather than an image, not fussed if its very simple/basic
• I am open to any colour but think I would prefer a more earthy sandy clay etc type style than the greens that are commonly associated with naturopathy.
Should not have
• Don't really want to have generic stock images on it

```html
<!DOCTYPE html>
<html lang="en">
<head>
<meta charset="utf-8">
<title>Tom Rudd Naturopath – Business Card</title>
<link href="https://fonts.googleapis.com/css2?family=Tinos:wght@700&family=Arimo:wght@400&display=swap" rel="stylesheet">
<style>
  :root {
    --page-bg: #ece9e4;
    --card-white: #ffffff;
    --card-blue: #dfe9f6;
    --rule-grey: #8d8fa6;
    --curve-green: #a9bf8a;
    --ink: #111111;
    --dotted: #333333;
    --chamomile: #5f8fd6;
    --spice: #8a4a2a;
    --ivy: #b9c7b4;
    --berry: #a83a2e;
  }
  * { margin: 0; padding: 0; box-sizing: border-box; }
  html, body { width: 1200px; height: 892px; overflow: hidden; background: var(--page-bg); }
  .canvas {
    width: 1200px; height: 892px;
    display: flex; align-items: center; justify-content: center; gap: 40px;
  }
  .card {
    position: relative; width: 540px; height: 309px;
    background: var(--card-white); overflow: hidden;
    box-shadow: 0 6px 18px rgba(0,0,0,.18);
  }
  .card-front .artwork { position: absolute; inset: 0; }
  .front-details {
    position: absolute; left: 240px; width: 280px; top: 140px;
    text-align: center; color: var(--ink);
    font-family: "Arimo", Arial, sans-serif;
  }
  .practitioner-name {
    font-family: "Tinos", "Times New Roman", serif; font-weight: 700;
    font-size: 30px; line-height: 1.05;
  }
  .practitioner-role { font-size: 16px; line-height: 1.15; }
  .practitioner-credentials { font-size: 16px; line-height: 1.2; white-space: nowrap; }
  .contact { margin-top: 14px; font-size: 15px; line-height: 1.25; }

  .card-back { padding: 26px 34px; font-family: "Arimo", Arial, sans-serif; color: var(--ink); }
  .appointment-title {
    font-family: "Tinos", "Times New Roman", serif; font-weight: 700;
    font-size: 40px; text-align: center; margin-bottom: 22px;
  }
  .form-row { display: flex; align-items: flex-end; gap: 8px; font-size: 17px; margin-bottom: 22px; }
  .fill-line { flex: 1; border-bottom: 2px dotted var(--dotted); height: 16px; }
  .day-options { display: flex; justify-content: space-between; font-size: 15px; margin: 4px 30px 22px 0; }
  .day { display: flex; align-items: center; gap: 3px; }
  .tick-box { width: 14px; height: 14px; border: 1.5px solid var(--ink); }
  .blank-line { border-bottom: 2px dotted var(--dotted); height: 10px; }
</style>
</head>
<body>
<main class="canvas">
  <section class="card card-front" aria-label="Business card front">
    <svg class="artwork" width="540" height="309" viewBox="0 0 540 309">
      <defs>
        <clipPath id="photo-strip">
          <path d="M0 58 H540 V64 C420 82 300 110 230 150 C170 185 140 240 130 309 H0 Z"/>
        </clipPath>
        <linearGradient id="chamomile-tone" x1="0" y1="0" x2="0" y2="1">
          <stop offset="0" stop-color="#e7eef6"/><stop offset="1" stop-color="var(--chamomile)"/>
        </linearGradient>
        <linearGradient id="spice-tone" x1="0" y1="0" x2="1" y2="1">
          <stop offset="0" stop-color="#6b8a4a"/><stop offset="1" stop-color="var(--spice)"/>
        </linearGradient>
        <linearGradient id="ivy-tone" x1="0" y1="0" x2="1" y2="1">
          <stop offset="0" stop-color="#e4e4df"/><stop offset="1" stop-color="var(--ivy)"/>
        </linearGradient>
        <linearGradient id="berry-tone" x1="0" y1="0" x2="1" y2="1">
          <stop offset="0" stop-color="#7fa070"/><stop offset="1" stop-color="var(--berry)"/>
        </linearGradient>
      </defs>
      <rect x="0" y="0" width="540" height="309" fill="var(--card-blue)"/>
      <rect x="0" y="0" width="540" height="56" fill="var(--card-white)"/>
      <g clip-path="url(#photo-strip)">
        <rect x="0" y="56" width="150" height="253" fill="url(#chamomile-tone)" role="img" aria-label="Photo of chamomile flowers and white homeopathic pills"/>
        <rect x="150" y="56" width="120" height="253" fill="url(#spice-tone)" role="img" aria-label="Photo of cinnamon, chillies and dried spices"/>
        <rect x="270" y="56" width="130" height="253" fill="url(#ivy-tone)" role="img" aria-label="Photo of a green leaf on glass capsules"/>
        <rect x="400" y="56" width="140" height="253" fill="url(#berry-tone)" role="img" aria-label="Photo of red hawthorn berries with leaves"/>
      </g>
      <path d="M540 64 C420 82 300 110 230 150 C170 185 140 240 130 309" fill="none" stroke="var(--curve-green)" stroke-width="1.5"/>
      <line x1="0" y1="50" x2="540" y2="50" stroke="var(--rule-grey)" stroke-width="1.2"/>
      <line x1="0" y1="58" x2="540" y2="58" stroke="var(--rule-grey)" stroke-width="1.2"/>
    </svg>
    <div class="front-details">
      <h1 class="practitioner-name">Tom Rudd</h1>
      <p class="practitioner-role">Naturopath</p>
      <p class="practitioner-credentials">BHSc (Naturopathy) Member WHPG</p>
      <p class="contact">0487 925 316<br>tom.rudd@mailexample.com</p>
    </div>
  </section>

  <section class="card card-back" aria-label="Business card back – appointment">
    <h2 class="appointment-title">Appointment</h2>
    <div class="form-row"><span>For:</span><span class="fill-line"></span></div>
    <div class="form-row"><span>Date:</span><span class="fill-line"></span><span>Time:</span><span class="fill-line"></span></div>
    <div class="day-options">
      <span class="day"><span class="tick-box"></span>TUE.</span>
      <span class="day"><span class="tick-box"></span>WED.</span>
      <span class="day"><span class="tick-box"></span>THUR.</span>
      <span class="day"><span class="tick-box"></span>FRI.</span>
      <span class="day"><span class="tick-box"></span>SAT.</span>
    </div>
    <div class="blank-line"></div>
  </section>
</main>
</body>
</html>
```